Business Card Design Project

i need a bussines car design
Velora Clinical Hypnotherapy

Daniel Wexford
Psychotherapy & Hypnosis

84261937 /0427591628

back of the card appoinment space.

file was provided on a PDF, LOgo , use the blu colorsa as well , elegant, clear,

Target Market(s)

young professional, caucasian , young mothers.

Industry/Entity Type

Business

```html
<!DOCTYPE html>
<html lang="en">
<head>
<meta charset="utf-8">
<title>Velora Clinical Hypnotherapy – Business Card</title>
<link href="https://fonts.googleapis.com/css2?family=Open+Sans:wght@300;400;600;700&display=swap" rel="stylesheet">
<style>
  :root{
    --bg:#d9dadb;
    --card:#fbfbfb;
    --blue-deep:#1f5e9c;
    --blue:#3f83c4;
    --blue-light:#8fb9e0;
    --ink:#2e2e2e;
    --grey:#7a7a7a;
  }
  *{box-sizing:border-box;margin:0;padding:0}
  html,body{width:1200px;height:907px;overflow:hidden}
  body{background:var(--bg);font-family:"Open Sans",Arial,sans-serif;color:var(--ink);position:relative}
  .card{position:absolute;width:600px;height:343px;background:var(--card);box-shadow:0 2px 6px rgba(0,0,0,.12);overflow:hidden}
  .card--front{left:300px;top:70px}
  .card--back{left:300px;top:494px}

  .brand-art{position:absolute;background:radial-gradient(ellipse at 50% 55%,var(--blue-deep) 0%,var(--blue) 45%,var(--blue-light) 80%,rgba(143,185,224,0) 100%);opacity:.85}
  .card--front .brand-art{left:0;top:0;width:230px;height:150px}
  .card--back .brand-art{right:0;top:0;width:120px;height:140px}

  .wordmark{position:absolute;display:flex;align-items:center;gap:8px;font-weight:300;color:var(--blue-deep);white-space:nowrap}
  .wordmark .dot{width:12px;height:12px;border-radius:50%;background:var(--blue)}
  .wordmark-rule{position:absolute;height:2px;background:var(--blue)}
  .website{position:absolute;font-size:12px;letter-spacing:.6px;color:var(--ink);font-weight:600;white-space:nowrap}

  .card--front .wordmark{left:250px;top:92px;font-size:28px}
  .card--front .wordmark-rule{left:250px;top:136px;width:320px}
  .card--front .website{left:252px;top:142px}

  .address{position:absolute;left:30px;top:192px;width:120px;text-align:right;font-size:12px;line-height:1.35;color:var(--grey)}
  .address .label{color:var(--blue);font-weight:700}
  .divider{position:absolute;left:162px;top:192px;width:1px;height:56px;background:var(--blue)}
  .phones{position:absolute;left:176px;top:196px;font-size:15px;color:var(--ink);line-height:1.55}
  .phones li{list-style:none;display:flex;align-items:center;gap:8px}
  .phones svg{width:12px;height:14px;fill:var(--blue)}
  .person{position:absolute;right:40px;top:262px;text-align:right}
  .person .name{font-size:22px;font-weight:700;color:var(--ink);letter-spacing:.3px}
  .person .role{font-size:12px;color:var(--ink);margin-top:6px}

  .card--back .wordmark{left:30px;top:28px;font-size:20px}
  .card--back .wordmark-rule{left:30px;top:60px;width:230px;height:1.5px}
  .card--back .website{left:30px;top:64px;font-size:9.5px;letter-spacing:.3px}
  .contact{position:absolute;left:30px;top:92px;font-size:9.5px;line-height:1.6;color:var(--ink)}
  .appointments{position:absolute;left:30px;top:150px;width:420px}
  .appointments h2{font-size:12px;font-weight:700;margin-bottom:6px}
  .appointments ol{list-style:none}
  .appointments li{font-size:11px;display:flex;align-items:flex-end;gap:6px;height:22px}
  .appointments .blank{display:inline-block;width:40px;border-bottom:1px solid var(--ink)}
  .appointments .date{flex:1;border-bottom:1px solid var(--ink);height:14px}
  .note{position:absolute;left:30px;top:292px;width:300px;font-size:7.5px;line-height:1.4;color:var(--ink)}
  .registration{position:absolute;left:350px;top:292px;font-size:9px;font-weight:700;line-height:1.35}
  .badge{position:absolute;right:40px;top:270px;width:54px;height:54px;border-radius:50%;background:linear-gradient(135deg,#e6d84a,#7cbf4a);border:2px solid #cfcfcf}
</style>
</head>
<body>

<section class="card card--front" aria-label="Card front">
  <div class="brand-art" role="img" aria-label="Brand symbol area"></div>
  <div class="wordmark"><span class="dot"></span>Velora Hypnotherapy</div>
  <div class="wordmark-rule"></div>
  <div class="website">www.veloraclinicalhypnotherapy.com.au</div>

  <div class="address"><div class="label">Clinic Address:</div>148 Kensal Road<br>Brookvale</div>
  <div class="divider"></div>
  <ul class="phones">
    <li><svg viewBox="0 0 12 14"><rect x="2" y="0" width="8" height="14" rx="1.5"/><rect x="3.5" y="2" width="5" height="8" fill="#fbfbfb"/></svg>0427 591 628</li>
    <li><svg viewBox="0 0 12 14"><rect x="0" y="3" width="12" height="11" rx="1.5"/><rect x="1" y="0" width="10" height="3" rx="1"/><rect x="3" y="6" width="6" height="5" fill="#fbfbfb"/></svg>842 61 937</li>
  </ul>
  <div class="person">
    <div class="name">DANIEL WEXFORD</div>
    <div class="role">Psychotherapy &amp; Hypnosis</div>
  </div>
</section>

<section class="card card--back" aria-label="Card back">
  <div class="brand-art" role="img" aria-label="Brand symbol area"></div>
  <div class="wordmark"><span class="dot"></span>Velora Hypnotherapy</div>
  <div class="wordmark-rule"></div>
  <div class="website">www.veloraclinicalhypnotherapy.com.au</div>
  <div class="contact">
    By Appointment · Phone: 0427 591 628<br>
    62 Harlow Street, Elmsford 3021<br>
    hello@veloraclinicalhypnotherapy.com.au
  </div>
  <div class="appointments">
    <h2>Your Appointments</h2>
    <ol>
      <li>1. <span class="blank"></span>am/pm <span class="date"></span>/ /</li>
      <li>2. <span class="blank"></span>am/pm <span class="date"></span>/ /</li>
      <li>3. <span class="blank"></span>am/pm <span class="date"></span>/ /</li>
      <li>4. <span class="blank"></span>am/pm <span class="date"></span>/ /</li>
      <li>5. <span class="blank"></span>am/pm <span class="date"></span>/ /</li>
    </ol>
  </div>
  <p class="note">To reschedule your appointment, please SMS or phone 0427 591 628 at least 24 hours prior to your allocated time. Thank you.</p>
  <div class="registration">VPTR Registration<br>No. NPM058214</div>
  <div class="badge" role="img" aria-label="Association membership badge"></div>
</section>

</body>
</html>
```